Graphic Design for a 3 Banner Tradeshow Setup

We are a Pipe Restoration company that specializes in trenchless pipelining. We need a design for a 3 banner setup to use at tradeshows. See attached "banner specs" for sizing - note the 48" x 92" will be in between the two 36" x 92" banners. See attached "Mock-Up" of information each banner needs and utilize the color scheme of the banners we already have in the "both DWM banners" AI file attached. The final designs should communicate what we do and attract people into our booth. We would like to have graphics of realistic pipes for a before (dirty pipe), after cleaning pipe, and lined pipe - see example of "pipe pictures" attached. I'm not sure if this is something you can generate or if we will need to find images of our own to send. Also, see attached "screenshot-process" to see similar images we would like to use to showcase the process.
Target Market(s)
Homeowners, Property Managers, HOA Communities, Healthcare Facilities & Hospitals, and commercial properties
Industry/Entity Type
Trenchless Pipelining
Look and feel

```html
<!DOCTYPE html>
<html lang="en">
<head>
<meta charset="utf-8">
<title>DWM Tradeshow Banners</title>
<link rel="stylesheet" href="https://fonts.googleapis.com/css2?family=Orbitron:wght@900&family=Poppins:wght@600;700&family=Roboto:wght@400;700&family=Oswald:wght@300;600&family=Rubik:wght@500&display=swap">
<style>
:root{
  --stage:#e3e2e4;
  --navy:#0e1830;
  --blue-deep:#102a5c;
  --blue-mid:#1b4d8c;
  --cyan:#1aa3e0;
  --silver:#b9bfc7;
  --light:#e6e8eb;
  --white:#ffffff;
  --ink:#1a2340;
}
*{margin:0;padding:0;box-sizing:border-box}
html,body{width:1200px;height:954px;overflow:hidden;background:var(--stage)}
.stage{position:relative;width:1200px;height:954px}
.banner{position:absolute;top:103px;height:690px;overflow:hidden;box-shadow:0 6px 14px rgba(0,0,0,.25)}
.banner--left{left:70px;width:270px}
.banner--center{left:407px;width:367px}
.banner--right{left:857px;width:270px}
.banner__bg{position:absolute;inset:0;width:100%;height:100%}
.brand{position:absolute;top:30px;left:0;right:0;text-align:center;color:var(--white)}
.brand__row{display:flex;justify-content:center;align-items:center;gap:6px}
.brand__mark{width:30px;height:30px;background:var(--cyan)}
.brand__name{font-family:"Orbitron",sans-serif;font-weight:900;font-size:36px;line-height:36px;letter-spacing:2px}
.brand__tag{font-family:"Roboto",sans-serif;font-size:8.5px;letter-spacing:1.6px;margin-top:4px}
.headline{position:absolute;left:0;right:0;text-align:center;font-family:"Orbitron",sans-serif;font-weight:900;color:var(--white);line-height:1}
.list{position:absolute;left:0;right:0;font-family:"Poppins",sans-serif;font-weight:700;color:var(--white)}
.item{position:absolute;left:0;right:0;text-align:center;font-size:17px}
.rule{position:absolute;border-top:1px dashed var(--cyan)}
.pitch{position:absolute;left:0;right:0;text-align:center;font-family:"Roboto",sans-serif;line-height:34px}
.pitch__accent{color:var(--cyan);font-weight:700;font-size:27px}
.pitch__plain{color:var(--white);font-weight:400;font-size:27px}
.pipes{position:absolute;left:16px;top:443px;width:330px;height:62px;border-radius:30px;background:linear-gradient(90deg,#7a4a2a,#a7683f 30%,#4fb6d4 48%,#55585c 62%,#c9ccd0 78%,#b33a22)}
.photo{position:absolute;left:176px;width:73px;height:55px;border:1px solid var(--white);background:linear-gradient(135deg,#3a6ea8,#8aa3b8)}
.fixes .item{text-align:left;left:27px;font-size:14px;line-height:18px}
.contact{position:absolute;left:0;right:0;top:560px;text-align:center}
.contact__cta{font-family:"Poppins",sans-serif;font-weight:600;font-size:13.5px;letter-spacing:2.2px;color:var(--ink)}
.phone{position:relative;margin:8px auto 0;height:26px;display:flex;align-items:center}
.phone__icon{position:absolute;left:0;top:-1px;width:28px;height:28px;border-radius:50%;background:var(--navy);display:flex;align-items:center;justify-content:center}
.phone__bar{margin-left:14px;height:26px;flex:1;background:var(--cyan);border:1px solid var(--white);color:var(--white);font-family:"Rubik",sans-serif;font-weight:500;font-size:23px;line-height:24px;text-align:center;padding-left:14px}
.web{font-family:"Oswald",sans-serif;font-size:16px;color:var(--ink);margin-top:8px;font-weight:300}
.web b{font-weight:600}
</style>
</head>
<body>
<div class="stage">

<svg width="0" height="0" style="position:absolute">
  <defs>
    <linearGradient id="bodyBlue" x1="0" y1="0" x2="0" y2="1">
      <stop offset="0" stop-color="#1d5596"/><stop offset="1" stop-color="#0f2755"/>
    </linearGradient>
    <linearGradient id="baseLight" x1="0" y1="0" x2="0" y2="1">
      <stop offset="0" stop-color="#f1f2f4"/><stop offset="1" stop-color="#d6d9dd"/>
    </linearGradient>
    <symbol id="bannerBg" viewBox="0 0 100 690" preserveAspectRatio="none">
      <rect width="100" height="690" fill="url(#baseLight)"/>
      <path d="M0,112 C35,90 60,82 100,100 L100,498 C60,478 35,482 0,510 Z" fill="url(#bodyBlue)"/>
      <path d="M0,0 H100 V94 C60,76 35,84 0,104 Z" fill="#0e1830"/>
      <path d="M0,108 C35,86 60,78 100,97" fill="none" stroke="#b9bfc7" stroke-width="6"/>
      <path d="M0,506 C35,478 60,474 100,494" fill="none" stroke="#b9bfc7" stroke-width="7"/>
    </symbol>
  </defs>
</svg>

<!-- Assess banner -->
<section class="banner banner--left">
  <svg class="banner__bg" preserveAspectRatio="none" viewBox="0 0 100 690"><use href="#bannerBg" width="100" height="690"/></svg>
  <div class="brand">
    <div class="brand__row"><span class="brand__mark"></span><span class="brand__name">DWM</span></div>
    <div class="brand__tag">DRAIN WORKS MASTERS</div>
  </div>
  <h1 class="headline" style="top:150px;font-size:32px">WE</h1>
  <h1 class="headline" style="top:184px;font-size:32px">ASSESS</h1>
  <div class="list">
    <p class="item" style="top:243px">CCTV Pipe Investigation</p>
    <span class="rule" style="top:284px;left:24px;right:22px"></span>
    <p class="item" style="top:302px">Budgetary Evaluation</p>
    <span class="rule" style="top:348px;left:24px;right:22px"></span>
    <p class="item" style="top:364px">Scope Development</p>
    <span class="rule" style="top:410px;left:24px;right:22px"></span>
    <p class="item" style="top:433px">Project Oversight</p>
  </div>
  <div class="contact">
    <p class="contact__cta">CONTACT US NOW!</p>
    <div class="phone" style="width:232px">
      <span class="phone__icon"><svg width="14" height="14" viewBox="0 0 24 24"><path fill="#fff" d="M6.6 10.8a15 15 0 0 0 6.6 6.6l2.2-2.2a1 1 0 0 1 1-.25 11 11 0 0 0 3.6.6 1 1 0 0 1 1 1V20a1 1 0 0 1-1 1A17 17 0 0 1 3 4a1 1 0 0 1 1-1h3.5a1 1 0 0 1 1 1 11 11 0 0 0 .6 3.6 1 1 0 0 1-.25 1z"/></svg></span>
      <span class="phone__bar">1-800-555-0142</span>
    </div>
    <p class="web">www.<b>drainworksmasters</b>.com</p>
  </div>
</section>

<!-- Center banner -->
<section class="banner banner--center">
  <svg class="banner__bg" preserveAspectRatio="none" viewBox="0 0 100 690"><use href="#bannerBg" width="100" height="690"/></svg>
  <div class="brand">
    <div class="brand__row"><span class="brand__mark"></span><span class="brand__name">DWM</span></div>
    <div class="brand__tag">DRAIN WORKS MASTERS</div>
  </div>
  <h1 class="headline" style="top:153px;font-size:42px">PIPE</h1>
  <h1 class="headline" style="top:198px;font-size:28px">PROBLEMS?</h1>
  <div class="pitch" style="top:242px">
    <p class="pitch__accent">WE HELP FIX PIPE<br>PROBLEMS</p>
    <p class="pitch__plain">WITHOUT HAVING<br>TO TEAR UP YOUR<br>BUIDLING</p>
  </div>
  <div class="pipes" role="img" aria-label="Three pipe sections: corroded dirty pipe, cleaned pipe, and newly lined pipe"></div>
  <div class="contact">
    <p class="contact__cta">CONTACT US NOW!</p>
    <div class="phone" style="width:236px">
      <span class="phone__icon"><svg width="14" height="14" viewBox="0 0 24 24"><path fill="#fff" d="M6.6 10.8a15 15 0 0 0 6.6 6.6l2.2-2.2a1 1 0 0 1 1-.25 11 11 0 0 0 3.6.6 1 1 0 0 1 1 1V20a1 1 0 0 1-1 1A17 17 0 0 1 3 4a1 1 0 0 1 1-1h3.5a1 1 0 0 1 1 1 11 11 0 0 0 .6 3.6 1 1 0 0 1-.25 1z"/></svg></span>
      <span class="phone__bar">1-800-555-0142</span>
    </div>
    <p class="web">www.<b>drainworksmasters</b>.com</p>
  </div>
</section>

<!-- Fix banner -->
<section class="banner banner--right">
  <svg class="banner__bg" preserveAspectRatio="none" viewBox="0 0 100 690"><use href="#bannerBg" width="100" height="690"/></svg>
  <div class="brand">
    <div class="brand__row"><span class="brand__mark"></span><span class="brand__name">DWM</span></div>
    <div class="brand__tag">DRAIN WORKS MASTERS</div>
  </div>
  <h1 class="headline" style="top:158px;left:25px;text-align:left;font-size:32px">WE FIX</h1>
  <div class="list fixes">
    <p class="item" style="top:211px">Slow Drains</p>
    <span class="rule" style="top:240px;left:27px;width:120px"></span>
    <p class="item" style="top:254px">Back-Ups</p>
    <span class="rule" style="top:287px;left:27px;width:120px"></span>
    <p class="item" style="top:299px">Sewer Odors</p>
    <span class="rule" style="top:333px;left:27px;width:120px"></span>
    <p class="item" style="top:347px">Cracked Pipes</p>
    <span class="rule" style="top:380px;left:27px;width:120px"></span>
    <p class="item" style="top:398px">Root Intrusion</p>
    <span class="rule" style="top:433px;left:27px;width:138px"></span>
    <p class="item" style="top:442px">Recurring Plumbing<br>Problems</p>
  </div>
  <div class="photo" style="top:203px" role="img" aria-label="Technician running a pipe inspection camera"></div>
  <div class="photo" style="top:276px" role="img" aria-label="Crew mixing lining resin on site"></div>
  <div class="photo" style="top:350px" role="img" aria-label="Two technicians preparing liner material"></div>
  <div class="contact">
    <p class="contact__cta">CONTACT US NOW!</p>
    <div class="phone" style="width:232px">
      <span class="phone__icon"><svg width="14" height="14" viewBox="0 0 24 24"><path fill="#fff" d="M6.6 10.8a15 15 0 0 0 6.6 6.6l2.2-2.2a1 1 0 0 1 1-.25 11 11 0 0 0 3.6.6 1 1 0 0 1 1 1V20a1 1 0 0 1-1 1A17 17 0 0 1 3 4a1 1 0 0 1 1-1h3.5a1 1 0 0 1 1 1 11 11 0 0 0 .6 3.6 1 1 0 0 1-.25 1z"/></svg></span>
      <span class="phone__bar">1-800-555-0142</span>
    </div>
    <p class="web">www.<b>drainworksmasters</b>.com</p>
  </div>
</section>

</div>
</body>
</html>
```